Professional Package for CPA Firm

We would like a stationery design for our new CPA Firm based in Atlanta, GA called 'Vale 8'. We work with investors to help grow investments, tax free. We would like the design to have a professional/minimal look with a 'wow' factor. We need 9.5″ x 4.125″, 9x12, and 10x13 mailing envelopes, business cards, and a letterhead. We have a logo that is already complete. For the letterhead, we would like to have space to put credentials at the bottom of the page

Industry/Entity Type

CPA, Accounting

```html
<!DOCTYPE html>
<html lang="en">
<head>
<meta charset="UTF-8">
<title>Vale 8 — Business Cards</title>
<link href="https://fonts.googleapis.com/css2?family=Montserrat:wght@500;700&family=Roboto:wght@400;500&display=swap" rel="stylesheet">
<style>
  :root {
    --backdrop: #2b2b2b;
    --card-white: #ffffff;
    --navy: #0f3a52;
    --ink: #16324a;
    --red: #e8434d;
    --teal: #1ea3b3;
    --grey-text: #555a60;
    --silver: #a9b3c1;
  }
  * { margin: 0; padding: 0; box-sizing: border-box; }
  html, body {
    width: 1200px; height: 900px; overflow: hidden;
    background: var(--backdrop);
  }
  .canvas {
    width: 1200px; height: 900px;
    display: flex; align-items: center; justify-content: center; gap: 36px;
  }
  .card {
    width: 540px; height: 308px; border-radius: 4px;
    position: relative; overflow: hidden;
  }

  /* front */
  .card-front { background: var(--card-white); }
  .brand {
    position: absolute; left: 44px; top: 70px;
    display: flex; flex-direction: column; align-items: flex-start;
  }
  .brand-mark { display: flex; align-items: center; gap: 10px; }
  .brand-dot { width: 14px; height: 14px; border-radius: 50%; background: var(--ink); }
  .brand-name {
    font-family: 'Montserrat', sans-serif; font-weight: 700;
    font-size: 36px; color: var(--ink); letter-spacing: 1px; line-height: 1;
  }
  .brand-tagline {
    font-family: 'Montserrat', sans-serif; font-weight: 500;
    font-size: 11px; color: var(--ink); margin-top: 8px; letter-spacing: .2px;
  }
  .divider {
    position: absolute; left: 262px; top: 150px;
    width: 1px; height: 118px; background: var(--ink); opacity: .75;
  }
  .contact {
    position: absolute; left: 288px; top: 138px;
    font-family: 'Roboto', sans-serif;
  }
  .person-name {
    font-family: 'Montserrat', sans-serif; font-weight: 700;
    font-size: 16px; color: var(--ink); letter-spacing: .3px; line-height: 1.2;
  }
  .person-title { font-size: 14px; color: var(--red); font-weight: 500; margin-top: 1px; }
  .address { font-size: 13px; color: var(--grey-text); margin-top: 8px; line-height: 1.35; }
  .contact-list { list-style: none; margin-top: 4px; }
  .contact-list li {
    display: flex; align-items: center; gap: 7px;
    font-size: 13px; color: var(--grey-text); line-height: 1.45;
  }
  .contact-list svg { width: 12px; height: 12px; flex: none; }

  /* back */
  .card-back {
    background: var(--navy);
    display: flex; flex-direction: column; align-items: center; justify-content: center;
  }
  .card-back .brand-name { color: var(--silver); font-size: 56px; }
  .card-back .brand-tagline { color: var(--silver); font-size: 15px; margin-top: 10px; }
</style>
</head>
<body>
<main class="canvas">
  <section class="card card-front">
    <div class="brand">
      <div class="brand-mark">
        <span class="brand-dot"></span>
        <span class="brand-name">VALE 8</span>
      </div>
      <p class="brand-tagline">CPAs and Tax Advisors</p>
    </div>
    <div class="divider"></div>
    <div class="contact">
      <h1 class="person-name">MARCUS HOLLANDER</h1>
      <p class="person-title">Managing Director</p>
      <p class="address">48 Linden Park Road,<br>Brookfield, ON M2K 4B7</p>
      <ul class="contact-list">
        <li>
          <svg viewBox="0 0 24 24"><path fill="#1ea3b3" d="M6.6 10.8a15 15 0 0 0 6.6 6.6l2.2-2.2c.3-.3.7-.4 1-.2 1.1.4 2.3.6 3.6.6.6 0 1 .4 1 1V20c0 .6-.4 1-1 1A17 17 0 0 1 3 4c0-.6.4-1 1-1h3.5c.6 0 1 .4 1 1 0 1.3.2 2.5.6 3.6.1.3 0 .7-.2 1z"/></svg>
          +5620437619
        </li>
        <li>
          <svg viewBox="0 0 24 24"><rect x="2" y="5" width="20" height="14" rx="2" fill="#1ea3b3"/><path d="M3 6l9 7 9-7" stroke="#fff" stroke-width="1.8" fill="none"/></svg>
          hello@valeeight.com
        </li>
        <li>
          <svg viewBox="0 0 24 24" fill="none" stroke="#1ea3b3" stroke-width="2"><circle cx="12" cy="12" r="9.5"/><ellipse cx="12" cy="12" rx="4" ry="9.5"/><path d="M2.5 12h19"/></svg>
          www.valeeight.com
        </li>
      </ul>
    </div>
  </section>

  <section class="card card-back">
    <span class="brand-name">VALE 8</span>
    <p class="brand-tagline">CPAs and Tax Advisors</p>
  </section>
</main>
</body>
</html>
```